Web Developer Needs a Business Card Design

I need a personal business card design that represents me as a web developer for potential employers. I would like the background to be a dark color on the front for contrast with my logo and name. The back will have all my information along with a smaller version of the logo. I want something with a modern look and feel, not too conservative. This will be used for potential employers and freelance work.

Industry/Entity Type

Business

Contact Information for Business Card

Front should have my logo and name. The back should have all my personal information which would include: name: Tom Varulek, phone: 570-614-3098, email: tomvarulek@quillbox.net, website url: www.tomvarulek.net, logo, web developer.

Font styles to use
Sans Serif

Requirements
Must have
• Must include my logo. The color palette base color will be the logo color.

```html
<!DOCTYPE html>
<html lang="en">
<head>
<meta charset="utf-8">
<title>Tom Varulek – Business Card</title>
<link rel="stylesheet" href="https://fonts.googleapis.com/css2?family=Open+Sans:wght@400;600;700&display=swap">
<style>
  :root {
    --backdrop: #e9e7e4;
    --card-white: #ffffff;
    --ink: #1c1c1c;
    --band-dark: #1e1e1e;
    --teal: #6fcab4;
    --teal-light: #a9e2d3;
    --teal-deep: #4fb89e;
    --front-top: #5a5a5a;
    --front-bottom: #151515;
    --white: #ffffff;
    --muted: #d8d8d8;
  }
  * { box-sizing: border-box; margin: 0; padding: 0; }
  html, body {
    width: 1200px; height: 913px; overflow: hidden;
    background: var(--backdrop);
    font-family: "Open Sans", sans-serif;
  }
  .canvas { position: relative; width: 1200px; height: 913px; }

  .card {
    position: absolute; top: 308px;
    width: 525px; height: 300px;
    border-radius: 4px; overflow: hidden;
    box-shadow: 0 10px 28px rgba(0,0,0,.22);
  }

  /* Back: contact side */
  .card--back { left: 45px; background: var(--card-white); }
  .back__stripe {
    position: absolute; left: 28px; top: 0; width: 88px; height: 100%;
    background: var(--band-dark);
  }
  .back__band {
    position: absolute; left: 116px; right: 0; top: 58px; height: 112px;
    background: linear-gradient(90deg, var(--teal-deep), var(--teal-light));
  }
  .back__contact {
    position: absolute; right: 26px; top: 66px; text-align: right;
    color: var(--ink);
  }
  .back__name { font-weight: 700; font-size: 19px; letter-spacing: .5px; line-height: 1.15; }
  .back__role { color: var(--white); font-size: 12px; letter-spacing: 1.5px; margin-bottom: 6px; }
  .contact-line {
    display: flex; justify-content: flex-end; align-items: center; gap: 6px;
    font-size: 13px; line-height: 1.45;
  }
  .contact-line svg { width: 11px; height: 11px; }

  .mark {
    position: absolute; border-radius: 50%;
    display: flex; align-items: center; justify-content: center; text-align: center;
    font-family: "Open Sans", sans-serif; font-weight: 700; color: var(--teal);
  }
  .back__mark {
    left: 52px; top: 128px; width: 128px; height: 128px;
    background: var(--card-white); border: 9px solid var(--teal);
    font-size: 16px; line-height: 1.15;
  }

  /* Front: name side */
  .card--front {
    left: 630px;
    background: linear-gradient(160deg, var(--front-top) 0%, #2c2c2c 45%, var(--front-bottom) 100%);
  }
  .front__mark {
    left: 205px; top: 36px; width: 115px; height: 115px;
    border: 8px solid var(--teal); background: transparent;
    font-size: 15px; line-height: 1.15;
  }
  .front__name {
    position: absolute; left: 0; right: 0; top: 170px; text-align: center;
    color: var(--white); font-size: 30px; font-weight: 400; letter-spacing: 3px;
  }
  .front__role {
    position: absolute; left: 0; right: 0; top: 218px; text-align: center;
    color: var(--muted); font-size: 15px; letter-spacing: .5px;
  }
</style>
</head>
<body>
<main class="canvas">

  <section class="card card--back" aria-label="Business card back with contact details">
    <div class="back__stripe"></div>
    <div class="back__band"></div>
    <div class="mark back__mark">Tom<br>Varulek</div>
    <div class="back__contact">
      <p class="back__name">TOM VARULEK</p>
      <p class="back__role">WEB DEVELOPER</p>
      <p class="contact-line">570-614-3098
        <svg viewBox="0 0 24 24" aria-hidden="true"><path fill="#1c1c1c" d="M6.6 10.8a15.1 15.1 0 0 0 6.6 6.6l2.2-2.2a1 1 0 0 1 1-.25 11.4 11.4 0 0 0 3.6.6 1 1 0 0 1 1 1V20a1 1 0 0 1-1 1A17 17 0 0 1 3 4a1 1 0 0 1 1-1h3.5a1 1 0 0 1 1 1c0 1.25.2 2.45.6 3.6a1 1 0 0 1-.25 1z"/></svg>
      </p>
      <p class="contact-line">tomvarulek@quillbox.net
        <svg viewBox="0 0 24 24" aria-hidden="true"><rect x="2" y="5" width="20" height="14" rx="1.5" fill="none" stroke="#1c1c1c" stroke-width="2"/><path d="M2.5 6l9.5 7 9.5-7" fill="none" stroke="#1c1c1c" stroke-width="2"/></svg>
      </p>
      <p class="contact-line">www.tomvarulek.net
        <svg viewBox="0 0 24 24" aria-hidden="true"><circle cx="12" cy="12" r="9.5" fill="none" stroke="#1c1c1c" stroke-width="2"/><path d="M2.5 12h19M12 2.5c3 3 3 16 0 19M12 2.5c-3 3-3 16 0 19" fill="none" stroke="#1c1c1c" stroke-width="1.6"/></svg>
      </p>
    </div>
  </section>

  <section class="card card--front" aria-label="Business card front with name">
    <div class="mark front__mark">Tom<br>Varulek</div>
    <h1 class="front__name">TOM VARULEK</h1>
    <p class="front__role">Front-End Developer</p>
  </section>

</main>
</body>
</html>
```